Website for Scientific & Engineering Organization

Overview

The objective is to design a professional, easy-to-navigate, and visually appealing website for the <Enclosed Organization (see attached files)>, reflecting their esteemed status in the engineering and scientific community.

Pages:

Home (About Us) : Introduce the organization, highlighting their activities, history, and fellowship. Include a section for latest news highlights.

News and Programme : Dedicated page for news updates and detailed annual programmes

Gallery : This page will feature photographs and descriptions of the society's 'Voyages' and events.

Downloads : A section offering downloadable content such as newsletters and lecture materials, organized for user-friendliness.

Members Section : A private area for members to access exclusive content. Alternatively, a 'Membership' page with joining details and benefits if more public-facing content is preferred.

Design Elements:

Layout : A linear layout with a fixed top navigation bar for easy movement between pages.
Color Scheme : Utilize the provided colors (#395394, #E00053, #0043E1) to create a cohesive and professional aesthetic.
Typography : Use a combination of serif for headings and sans-serif for body text, ensuring readability and elegance.

Features:

Responsive Design : The design will accommodate various devices, ensuring consistency across mobiles, tablets, and desktops.

Accessibility : Design for all users with adequate spacing around elements and color contrasts

Content Strategy (Visual Focus):

Home Page : Visual emphasis on the introduction, mission, and recent 'Voyages' with engaging imagery and concise text.
News and Programme : Clear, visually distinct sections for news and the annual schedule
Gallery : A visually rich page with a grid or album layout, allowing users to easily browse through the years and events.
Downloads : Neatly organized sections with clear labels and icons to represent the different types of available downloads. Downloads are PDF newsletter/flyers/programmes etc...
Members Section/Membership : A design that conveys exclusivity and value, encouraging sign-ups and engagement from members.
Design Considerations:

Consistency : Ensure the design reflects the organization's heritage and professionalism throughout all pages.
User Experience : Focus on intuitive navigation and information architecture to guide visitors smoothly through the site.
Visual Hierarchy : Use size, color, and layout to emphasize key areas and direct user attention effectively.
Final Notes:

This design spec focuses on creating a web presence that mirrors the organization's prestige and heritage, providing an engaging, informative platform for members and the public alike. The design will be crafted to allow for easy content updates and adaptability, ensuring a long-lasting and effective website.

Target Market(s)

Non profit science and engineering. Older people

Industry/Entity Type

Non profit scientific organization

Number of Pages Required

5+ page

Requirements
Should not have
• No search feature

```html
<!DOCTYPE html>
<html lang="en">
<head>
<meta charset="utf-8">
<title>ASEF British Section – Home</title>
<link href="https://fonts.googleapis.com/css2?family=Poppins:wght@400;500;600;700&display=swap" rel="stylesheet">
<style>
:root{
  --navy:#395394;
  --navy-dark:#2c4380;
  --pink:#E00053;
  --pink-dark:#b80045;
  --blue:#0043E1;
  --ink:#1d1d1f;
  --muted:#555a66;
  --white:#ffffff;
  --footer:#0f1013;
  --line:#e6e8ee;
}
*{box-sizing:border-box;margin:0;padding:0}
html,body{width:1200px;height:4440px;overflow:hidden}
body{font-family:"Poppins",sans-serif;color:var(--ink);background:var(--white);position:relative}
.brand{display:flex;align-items:center;gap:10px;font-family:"Poppins",sans-serif;font-weight:700;font-size:34px;color:var(--navy);letter-spacing:1px}
.brand-square{width:22px;height:22px;background:var(--pink)}
.btn{display:inline-block;background:var(--pink);color:var(--white);font-weight:600;font-size:15px;padding:11px 22px;border-radius:3px;text-decoration:none}
.btn-sm{font-size:13px;padding:9px 18px}

/* header */
.site-header{position:absolute;top:0;left:0;width:1200px;height:100px;display:flex;align-items:center;justify-content:space-between;padding:0 120px;background:var(--white);z-index:5;box-shadow:0 2px 6px rgba(0,0,0,.06)}
.main-nav{display:flex;gap:28px;font-size:15px;font-weight:500}
.main-nav a{color:var(--ink);text-decoration:none}

/* hero */
.hero{position:absolute;top:100px;left:0;width:1200px;height:640px;overflow:hidden}
.hero-photo{position:absolute;inset:0;background:linear-gradient(100deg,#1b2233 0%,#3b4659 45%,#8a8f94 75%,#b49868 100%)}
.hero-content{position:absolute;left:120px;top:170px;color:var(--white)}
.hero-brand{font-weight:700;font-size:42px;display:flex;align-items:center;gap:12px;margin-bottom:4px}
.hero-brand .brand-square{background:var(--white);width:26px;height:26px}
.hero-sub{font-size:12px;line-height:1.3;margin-bottom:34px;opacity:.9}
.hero-title{font-weight:700;font-size:31px;line-height:1.3;text-transform:uppercase;margin-bottom:26px}
.hero-dots{display:flex;gap:8px;margin-top:60px}
.hero-dots span{width:10px;height:10px;border-radius:50%;background:rgba(255,255,255,.5)}
.hero-dots span:first-child{background:var(--white)}
.hero-wave{position:absolute;left:0;bottom:0;width:1200px;height:130px}

/* intro cards */
.intro{position:absolute;top:820px;left:0;width:1200px;display:flex;justify-content:center;gap:40px}
.intro-card{width:290px;height:340px;background:var(--white);border-radius:6px;box-shadow:0 4px 18px rgba(0,0,0,.1);overflow:hidden;text-align:center}
.intro-photo{height:190px;margin:14px 14px 0;border-radius:4px}
.intro-card p{font-size:13px;line-height:1.55;color:var(--muted);padding:18px 20px 0}
.intro-card h3{font-size:15px;font-weight:600;padding:26px 20px 14px;line-height:1.4}

/* about */
.about{position:absolute;top:1180px;left:0;width:1200px;height:580px}
.about-bg{position:absolute;inset:0}
.about-mark{position:absolute;left:160px;top:110px;width:340px;height:340px;border-radius:50%;border:3px solid rgba(255,255,255,.18)}
.about-content{position:absolute;left:740px;top:150px;width:380px;color:var(--white)}
.about-content h2{font-size:40px;font-weight:700;margin-bottom:10px}
.about-content p{font-size:15px;line-height:1.6;margin-bottom:22px}

/* activities */
.explore{position:absolute;top:1830px;left:120px;width:960px;display:flex;gap:16px}
.explore-tile{position:relative;width:472px;height:360px;border-radius:4px;overflow:hidden}
.explore-tile .tile-photo{position:absolute;inset:0}
.tile-text{position:absolute;left:28px;bottom:24px;color:var(--white);width:330px}
.tile-text h3{font-size:22px;font-weight:700;margin-bottom:4px}
.tile-text p{font-size:12px;line-height:1.5;margin-bottom:6px}
.tile-text a{color:var(--white);font-size:13px;font-weight:600;text-decoration:underline}

/* members */
.members{position:absolute;top:2280px;left:0;width:1200px;text-align:center}
.members h2{font-size:36px;font-weight:700;margin-bottom:16px}
.members p{font-size:14px;line-height:1.6;color:var(--muted);width:1000px;margin:0 auto 20px}
.members-photo{position:absolute;top:2470px;left:0;width:1200px;height:410px;background:linear-gradient(180deg,#c9b49a 0%,#7a5a3c 45%,#3a2a1f 100%)}
.members-photo span{position:absolute;right:20px;bottom:26px;color:var(--white);font-size:26px;font-weight:600}

/* pink band */
.mission{position:absolute;top:2880px;left:0;width:1200px;height:300px;background:var(--pink);text-align:center;color:var(--white)}
.mission h2{width:880px;margin:70px auto 18px;font-size:27px;font-weight:700;line-height:1.4}
.mission p{font-size:14px}
.mission-wave{position:absolute;left:0;bottom:-1px;width:1200px;height:90px}

/* events */
.events{position:absolute;top:3270px;left:0;width:1200px}
.events h2{text-align:center;font-size:36px;font-weight:700;margin-bottom:36px}
.event-list{display:flex;justify-content:center;gap:36px}
.event-card{width:300px;height:410px;background:var(--white);border-radius:6px;box-shadow:0 4px 18px rgba(0,0,0,.1);padding:12px}
.event-photo{height:190px;border-radius:4px;margin-bottom:12px}
.event-date{display:flex;align-items:center;gap:6px;font-size:13px;color:var(--pink);margin-bottom:6px}
.event-card h3{font-size:14px;font-weight:600;line-height:1.4;margin-bottom:10px}
.event-card h4{font-size:14px;font-weight:700;line-height:1.4}
.event-card .event-note{font-size:12px;color:var(--muted);margin-bottom:12px;line-height:1.4}
.slider-arrow{position:absolute;top:3540px;width:22px;height:22px;border-radius:50%;background:var(--navy)}
.slider-arrow svg{display:block}

/* footer */
.site-footer{position:absolute;top:3790px;left:0;width:1200px;height:650px;background:var(--footer);color:var(--white)}
.footer-wave{position:absolute;top:-1px;left:0;width:1200px;height:110px}
.footer-cols{position:absolute;top:200px;left:120px;width:960px;display:flex}
.footer-brand{width:320px}
.footer-brand .brand{color:var(--white)}
.footer-brand small{display:block;font-size:12px;color:#cfd3dc;margin-top:6px;line-height:1.4}
.footer-col h4{font-size:19px;font-weight:600;margin-bottom:18px}
.footer-links{width:190px}
.footer-links a{display:block;color:#d9dbe2;font-size:14px;text-decoration:none;margin-bottom:10px}
.footer-contact{width:270px;font-size:13px;line-height:1.5;color:#d9dbe2}
.contact-item{display:flex;gap:8px;margin-bottom:14px}
.contact-item strong{display:block;color:var(--white);font-weight:600}
.footer-news{width:200px;font-size:13px;color:#d9dbe2;line-height:1.5}
.news-input{height:34px;background:var(--white);margin:16px 0 8px;border-radius:2px}
.news-btn{height:34px;background:var(--pink);color:var(--white);font-size:12px;font-weight:600;display:flex;align-items:center;justify-content:center;letter-spacing:1px}
.copyright{position:absolute;bottom:22px;left:0;width:1200px;text-align:center;font-size:12px;color:#b9bdc7;border-top:1px solid #2a2c33;padding-top:14px}
</style>
</head>
<body>

<header class="site-header">
  <div class="brand"><span class="brand-square"></span>ASEF</div>
  <nav class="main-nav">
    <a href="#">About Us</a><a href="#">News &amp; Programme</a><a href="#">Gallery</a><a href="#">Downloads</a><a href="#">Contact Us</a><a href="#">Members Section</a>
  </nav>
</header>

<section class="hero">
  <div class="hero-photo" role="img" aria-label="Engineer in a hard hat working on a laptop at an industrial site"></div>
  <div class="hero-content">
    <div class="hero-brand"><span class="brand-square"></span>ASEF</div>
    <div class="hero-sub">Alliance des Savants<br>et Experts de France</div>
    <h1 class="hero-title">Welcome to the British Section of the ASEF<br>Sharing Knowledge and a Love of France</h1>
    <a class="btn" href="#">Get Started</a>
    <div class="hero-dots"><span></span><span></span><span></span></div>
  </div>
  <svg class="hero-wave" viewBox="0 0 1200 130" preserveAspectRatio="none">
    <path d="M0 60 C300 140 700 20 1200 50 L1200 130 L0 130Z" fill="var(--pink)"/>
    <path d="M0 85 C320 150 720 50 1200 80 L1200 130 L0 130Z" fill="var(--white)"/>
  </svg>
</section>

<section class="intro">
  <article class="intro-card">
    <div class="intro-photo" role="img" aria-label="Engineers inspecting a construction site" style="background:linear-gradient(135deg,#c9a27a,#6d7e92)"></div>
    <p>An informal society of engineers and scientists, giving equal importance to the quality of our technical activities and our fellowship.</p>
  </article>
  <article class="intro-card">
    <div class="intro-photo" role="img" aria-label="Scientist working in a laboratory" style="background:linear-gradient(135deg,#2a5b8c,#a9c8e0)"></div>
    <p>We provide high quality lectures and technical visits on diverse engineering and scientific subjects, and the enjoyment of French food and Cuisine.</p>
  </article>
  <article class="intro-card">
    <div class="intro-photo" role="img" aria-label="Researchers discussing work in a lab" style="background:linear-gradient(135deg,#e8edf3,#9fb4c9)"></div>
    <h3>New members are always welcome</h3>
    <a class="btn btn-sm" href="#">Learn More</a>
  </article>
</section>

<section class="about">
  <svg class="about-bg" viewBox="0 0 1200 580" preserveAspectRatio="none">
    <defs><linearGradient id="aboutGrad" x1="0" y1="0" x2="1" y2="1"><stop offset="0" stop-color="#4a64b0"/><stop offset="1" stop-color="#2c4380"/></linearGradient></defs>
    <path d="M0 50 C400 0 800 90 1200 30 L1200 540 C800 600 400 500 0 560Z" fill="url(#aboutGrad)"/>
  </svg>
  <div class="about-mark"></div>
  <div class="about-content">
    <h2>ABOUT US</h2>
    <p>We are an informal society of engineers and scientists. A very friendly organisation where equal importance is given to the quality of our technical activities and our fellowship, where our partners are involved and welcomed in everything we do.</p>
    <a class="btn btn-sm" href="#">Read More</a>
  </div>
</section>

<section class="explore">
  <article class="explore-tile">
    <div class="tile-photo" role="img" aria-label="Members visiting a historic building" style="background:linear-gradient(180deg,#c79a95 0%,#8a5c60 60%,#3b2a30 100%)"></div>
    <div class="tile-text">
      <h3>Our Activities</h3>
      <p>Find out about our lectures, technical visits and voyages held throughout the year, many followed by dinner.</p>
      <a href="#">Read Activities</a>
    </div>
  </article>
  <article class="explore-tile">
    <div class="tile-photo" role="img" aria-label="Suspension bridge over a river" style="background:linear-gradient(180deg,#cfd4d8 0%,#8b949b 55%,#3d4a45 100%)"></div>
    <div class="tile-text">
      <h3>Our History</h3>
      <a href="#">Read Activities</a>
    </div>
  </article>
</section>

<section class="members">
  <h2>OUR MEMBERS</h2>
  <p>The origins of the Section lie in civil engineering. For many years, however, in line with the now named Alliance des Savants et Experts de France (ASEF), we have been open to membership from like-minded people from all fields of engineering and science. We are always delighted to welcome new members. If you would like to join us or would like further information on membership,</p>
  <a class="btn btn-sm" href="#">Please Click Membership</a>
</section>
<div class="members-photo" role="img" aria-label="Members seated at a formal banquet in a grand hall"><span>Celebrating our Centenary</span></div>

<section class="mission">
  <h2>The Society For Engineers And Scientists Where They Sample French Cuisine And Culture With Their Partners As Well As Continue Their Professional Interests</h2>
  <p>And Annual General Meetings the Hall of Engineers, 12 Bridge Row</p>
  <svg class="mission-wave" viewBox="0 0 1200 90" preserveAspectRatio="none">
    <path d="M0 40 C400 100 800 0 1200 50 L1200 90 L0 90Z" fill="var(--white)"/>
  </svg>
</section>

<section class="events">
  <h2>UPCOMING EVENTS</h2>
  <div class="event-list">
    <article class="event-card">
      <div class="event-photo" role="img" aria-label="Fire investigator examining a burnt site" style="background:linear-gradient(160deg,#4b4b4d,#c48a3a)"></div>
      <div class="event-date"><svg width="13" height="13" viewBox="0 0 14 14"><rect x="1" y="2" width="12" height="11" rx="1" fill="none" stroke="currentColor" stroke-width="1.5"/><line x1="1" y1="5.5" x2="13" y2="5.5" stroke="currentColor" stroke-width="1.5"/></svg>Monday 29 January 2024</div>
      <h3>Incoming President's Inaugural lecture and dinner</h3>
      <h4>Forensic Fire Investigation :</h4>
      <p class="event-note">The Underpinning Fire Science And Investigation Methodology</p>
      <a class="btn btn-sm" href="#">Learn More</a>
    </article>
    <article class="event-card">
      <div class="event-photo" role="img" aria-label="Wildfire burning near houses" style="background:linear-gradient(160deg,#e0651a,#5a1a0c)"></div>
      <div class="event-date"><svg width="13" height="13" viewBox="0 0 14 14"><rect x="1" y="2" width="12" height="11" rx="1" fill="none" stroke="currentColor" stroke-width="1.5"/><line x1="1" y1="5.5" x2="13" y2="5.5" stroke="currentColor" stroke-width="1.5"/></svg>Tuesday 19 March 2024</div>
      <h3>Evening Lecture and Dinner</h3>
      <h4>How To Protect People And Homes From Wildfires :</h4>
      <p class="event-note">&nbsp;</p>
      <a class="btn btn-sm" href="#">Learn More</a>
    </article>
    <article class="event-card">
      <div class="event-photo" role="img" aria-label="Tower block fire with smoke against the sky" style="background:linear-gradient(160deg,#9aa5b1,#3b3d42)"></div>
      <div class="event-date"><svg width="13" height="13" viewBox="0 0 14 14"><rect x="1" y="2" width="12" height="11" rx="1" fill="none" stroke="currentColor" stroke-width="1.5"/><line x1="1" y1="5.5" x2="13" y2="5.5" stroke="currentColor" stroke-width="1.5"/></svg>Tuesday 30 April 2024</div>
      <h3>Evening Lecture and Dinner</h3>
      <h4>Unplanned Adventures In Fire Science, Engineering, And Regulation</h4>
      <p class="event-note">&nbsp;</p>
      <a class="btn btn-sm" href="#">Learn More</a>
    </article>
  </div>
</section>
<div class="slider-arrow" style="left:40px"><svg width="22" height="22" viewBox="0 0 22 22"><path d="M13 6 L8 11 L13 16" fill="none" stroke="#fff" stroke-width="2"/></svg></div>
<div class="slider-arrow" style="left:1138px"><svg width="22" height="22" viewBox="0 0 22 22"><path d="M9 6 L14 11 L9 16" fill="none" stroke="#fff" stroke-width="2"/></svg></div>

<footer class="site-footer">
  <svg class="footer-wave" viewBox="0 0 1200 110" preserveAspectRatio="none">
    <path d="M0 0 L1200 0 L1200 60 C800 120 400 20 0 80Z" fill="var(--pink)"/>
    <path d="M0 0 L1200 0 L1200 40 C800 95 400 0 0 55Z" fill="var(--white)"/>
  </svg>
  <div class="footer-cols">
    <div class="footer-brand">
      <div class="brand"><span class="brand-square"></span>ASEF</div>
      <small>Alliance des Savants<br>et Experts de France</small>
    </div>
    <div class="footer-col footer-links">
      <h4>Quick Links</h4>
      <a href="#">About Us</a><a href="#">News &amp; Programme</a><a href="#">Gallery</a><a href="#">Downloads</a><a href="#">Contact Us</a><a href="#">Members Section</a>
    </div>
    <div class="footer-col footer-contact">
      <h4>Contact Details</h4>
      <div class="contact-item"><svg width="14" height="16" viewBox="0 0 14 16"><path d="M7 1a5 5 0 0 1 5 5c0 4-5 9-5 9S2 10 2 6a5 5 0 0 1 5-5z" fill="var(--pink)"/><circle cx="7" cy="6" r="2" fill="var(--footer)"/></svg><div><strong>Address :</strong>ASEF British Section Secretariat c/o Claire Henley, Hall of Engineers, 12 Bridge Row, Westminster, London, SW1A 0ZZ</div></div>
      <div class="contact-item"><svg width="14" height="14" viewBox="0 0 14 14"><path d="M3 1 L5 1 L6 4 L4.5 5.5 A8 8 0 0 0 8.5 9.5 L10 8 L13 9 L13 11 A2 2 0 0 1 11 13 A10 10 0 0 1 1 3 A2 2 0 0 1 3 1Z" fill="var(--pink)"/></svg><div><strong>Telephone :</strong>020 7946 0183</div></div>
      <div class="contact-item"><svg width="14" height="12" viewBox="0 0 14 12"><rect x="0.5" y="1" width="13" height="10" rx="1" fill="var(--pink)"/><path d="M1 2 L7 7 L13 2" fill="none" stroke="var(--footer)" stroke-width="1.2"/></svg><div><strong>E - mail :</strong>claire.henley@asef-example.org</div></div>
    </div>
    <div class="footer-col footer-news">
      <h4>Newsletter</h4>
      <p>Stay up to date with our latest lectures, visits and news.</p>
      <div class="news-input"></div>
      <div class="news-btn">SUBSCRIBE</div>
    </div>
  </div>
  <div class="copyright">© Copyright 2023 ASEF | All Rights Reserved</div>
</footer>

</body>
</html>
```